New Business Card for Web Design/Internet Marketing Company

Looking for a great looking new business card. We are a 10 year old web design, internet marketing and website management company that works mostly with small businesses.

Our new card needs to better match the colors and style of our website, be bold, extremely usable and slightly edgy.

Target Market(s)

Small/Medium businesses that have websites

Industry/Entity Type

Internet

Requirements
Must have
• Front and back design, full color, rounded corners please

Must use the colors/style of our website (JPG provided)

INFO FOR CARDS (as readable as possible please)
Mark Lenner
President/CEO
mark@trelvanmedia.example
Phone: 520-381-7459
Toll Free: 866-381-7459
Address: 4315 W. Calloway Ave. Ste. 140, Tucson, AZ 85792

THINGS I WANT TO PROMOTE (if there is room):
1. Our Website - www.trelvanmedia.example

2. Social Media
Twitter: @trelvanmedia
Facebook: www.facebook.com/trelvanmedia

3. Our Services
Web Design
Internet Marketing
Website Management

```html
<!DOCTYPE html>
<html lang="en">
<head>
<meta charset="utf-8">
<title>Trelvan Media – Business Card</title>
<link rel="stylesheet" href="https://fonts.googleapis.com/css2?family=Open+Sans:wght@400;600;700&display=swap">
<style>
  :root {
    --stage: #e9e6e2;
    --brand-blue: #0b8fd0;
    --brand-blue-dark: #0a7fbb;
    --brand-orange: #f07f22;
    --ink: #4a4a4a;
    --white: #ffffff;
  }
  * { box-sizing: border-box; margin: 0; padding: 0; }
  html, body {
    width: 1200px; height: 402px; overflow: hidden;
    background: var(--stage);
    font-family: "Open Sans", Arial, sans-serif;
  }
  .card {
    position: absolute; top: 57px;
    width: 515px; height: 292px;
    border-radius: 10px; overflow: hidden;
    box-shadow: 0 2px 6px rgba(0,0,0,.18);
  }
  .card--front { left: 62px; background: var(--white); }
  .card--back { left: 626px; background: var(--brand-blue); color: var(--white); text-align: center; }

  .front-swoosh { position: absolute; inset: 0; }

  .brand-name {
    position: absolute; left: 40px; top: 118px;
    font-size: 32px; font-weight: 700; letter-spacing: -0.5px;
    color: var(--brand-orange); line-height: 1;
  }
  .brand-mark {
    display: inline-block; width: 14px; height: 14px; border-radius: 50%;
    background: var(--brand-blue); margin-right: 8px; vertical-align: 3px;
  }

  .person { position: absolute; right: 26px; top: 34px; text-align: right; color: var(--brand-blue); }
  .person__name { font-size: 17px; font-weight: 700; }
  .person__title { font-size: 12px; }

  .address { position: absolute; left: 46px; top: 212px; font-size: 12px; line-height: 20px; color: var(--ink); }

  .contacts {
    position: absolute; right: 20px; top: 210px;
    list-style: none; text-align: right;
    font-size: 12px; line-height: 19px; color: var(--white);
  }
  .contacts svg { width: 10px; height: 10px; margin-left: 4px; vertical-align: -1px; }

  .back-brand {
    position: absolute; top: 60px; left: 0; right: 0;
    font-size: 38px; font-weight: 700; color: var(--white); line-height: 1;
  }
  .back-brand .brand-mark { width: 16px; height: 16px; background: var(--brand-orange); vertical-align: 5px; }

  .services { position: absolute; top: 158px; left: 0; right: 0; }
  .services__title {
    display: inline-block; font-size: 21px; font-weight: 600;
    padding: 0 14px 3px; border-bottom: 2px solid var(--white);
  }
  .services__list { margin-top: 12px; font-size: 18.5px; line-height: 27px; }

  .social {
    position: absolute; top: 266px; left: 0; right: 0;
    display: flex; justify-content: center; gap: 36px; font-size: 12px;
  }
  .social__icon {
    display: inline-block; width: 11px; height: 11px; border-radius: 2px;
    background: rgba(255,255,255,.8); margin-right: 5px; vertical-align: -1px;
  }
</style>
</head>
<body>
  <section class="card card--front">
    <svg class="front-swoosh" viewBox="0 0 515 292" preserveAspectRatio="none" aria-hidden="true">
      <path d="M0 262 C 150 255, 330 200, 515 150 L 515 292 L 0 292 Z" fill="var(--brand-blue)"/>
      <path d="M0 252 C 120 268, 220 250, 330 226" fill="none" stroke="var(--brand-orange)" stroke-width="5" stroke-linecap="round"/>
    </svg>

    <div class="brand-name"><span class="brand-mark"></span>Trelvan Media</div>

    <div class="person">
      <div class="person__name">Mark Lenner</div>
      <div class="person__title">President/CEO</div>
    </div>

    <address class="address" style="font-style:normal">
      4315 W. Calloway Ave. Ste. 140<br>
      Tucson, AZ 85792
    </address>

    <ul class="contacts">
      <li>520-381-7459<svg viewBox="0 0 10 10"><path d="M2 1 L4 1 L4.6 3 L3.4 3.8 Q4.5 6 6.2 6.6 L7 5.4 L9 6 L9 8 Q5 9 2 5 Q1 3 2 1Z" fill="var(--white)"/></svg></li>
      <li>866-381-7459<svg viewBox="0 0 10 10"><path d="M2 1 L4 1 L4.6 3 L3.4 3.8 Q4.5 6 6.2 6.6 L7 5.4 L9 6 L9 8 Q5 9 2 5 Q1 3 2 1Z" fill="var(--white)"/></svg></li>
      <li>mark@trelvanmedia.example<svg viewBox="0 0 10 10"><rect x="0.5" y="2" width="9" height="6.5" fill="var(--white)"/><path d="M0.5 2 L5 5.5 L9.5 2" fill="none" stroke="var(--brand-blue)" stroke-width="0.8"/></svg></li>
      <li>www.trelvanmedia.example<svg viewBox="0 0 10 10"><circle cx="5" cy="5" r="4.3" fill="none" stroke="var(--white)" stroke-width="1"/><path d="M0.7 5 H9.3 M5 0.7 Q2.5 5 5 9.3 M5 0.7 Q7.5 5 5 9.3" fill="none" stroke="var(--white)" stroke-width="0.8"/></svg></li>
    </ul>
  </section>

  <section class="card card--back">
    <div class="back-brand"><span class="brand-mark"></span>Trelvan Media</div>

    <div class="services">
      <h2 class="services__title">Our Services</h2>
      <p class="services__list">Web Design &nbsp;•&nbsp; Internet Marketing<br>Website Management</p>
    </div>

    <div class="social">
      <span><span class="social__icon"></span>@trelvanmedia</span>
      <span><span class="social__icon"></span>trelvanmedia</span>
    </div>
  </section>
</body>
</html>
```